"Leibeswerkstatt" private practice for physiotherapy

we are looking for a flyer design for a private practice for physiotherapy. the name of the practice is "Leibeswerkstatt".
Treatments such as: manual therapy, manual lymphatic drainage, classic massage, sectoral alternative practitioners are offered

The flyers should be double-sided and the format DIN long (105x210 mm)

Font styles to use
Serif

Colors
0094D4
00A9DD
6FCCEA
C7EBF8
E9F6FB

Requirements
Must have
• Leibeswerkstatt, Lindenweg 17, 06548 Sangerhausen / Leibeswerkstatt-beispielort.de / Tel. 03464 7183520

```html
<!DOCTYPE html>
<html lang="en">
<head>
<meta charset="utf-8">
<title>Leibeswerkstatt – Physiotherapy Flyer</title>
<link href="https://fonts.googleapis.com/css2?family=Poppins:wght@300;400;500;600;700;800&display=swap" rel="stylesheet">
<style>
  :root {
    --page-bg: #5a5c60;
    --blue: #0094d4;
    --blue-bright: #00a9dd;
    --blue-light: #6fccea;
    --blue-pale: #c7ebf8;
    --blue-mist: #e9f6fb;
    --navy: #14304a;
    --aqua: #3ee6d4;
    --white: #ffffff;
    --grey-text: #6b6b6d;
  }
  * { margin: 0; padding: 0; box-sizing: border-box; }
  html, body { width: 1200px; height: 800px; overflow: hidden; }
  body {
    background: var(--page-bg);
    font-family: "Poppins", sans-serif;
    position: relative;
  }
  .flyer {
    position: absolute;
    top: 60px;
    width: 340px;
    height: 680px;
    overflow: hidden;
    box-shadow: 0 6px 18px rgba(0,0,0,.35);
  }
  .flyer--front { left: 330px; background: var(--blue); }
  .flyer--back { left: 725px; background: var(--navy); }

  /* Front */
  .front-title {
    position: absolute; left: 24px; top: 52px;
    font-size: 27px; font-weight: 700; color: var(--white); letter-spacing: .3px;
  }
  .front-rule {
    position: absolute; left: 26px; top: 89px; width: 92px; height: 2px; background: var(--white);
  }
  .front-subtitle {
    position: absolute; left: 26px; top: 92px;
    font-size: 20px; font-weight: 400; color: var(--blue-mist);
  }
  .front-art { position: absolute; left: 0; top: 0; }
  .front-overlay-word {
    position: absolute; left: 0; width: 340px; top: 308px; text-align: center;
    font-size: 33px; font-weight: 800; color: var(--grey-text); letter-spacing: .5px;
  }
  .front-contact {
    position: absolute; left: 0; width: 340px; top: 536px; text-align: center; color: var(--white);
  }
  .front-contact .name { font-size: 14px; font-weight: 600; }
  .front-contact .address { font-size: 13.5px; font-weight: 300; line-height: 17px; margin-top: 4px; }
  .front-contact .tel { font-size: 13.5px; font-weight: 500; margin-top: 8px; }

  /* Back */
  .back-intro {
    position: absolute; left: 0; top: 0; width: 340px; height: 106px;
    padding: 22px 30px 0; text-align: center;
    font-size: 13px; line-height: 16.5px; color: var(--white); font-weight: 400;
  }
  .back-photo { position: absolute; left: 0; top: 106px; width: 340px; height: 439px; }
  .back-lead {
    position: absolute; left: 0; width: 340px; top: 130px; text-align: center;
    font-size: 14px; line-height: 16.5px; font-weight: 500; color: var(--aqua);
  }
  .back-lead-rule {
    position: absolute; left: 97px; top: 170px; width: 146px; height: 2px; background: var(--white);
  }
  .service-list { position: absolute; left: 45px; top: 197px; list-style: none; }
  .service {
    display: flex; align-items: center; height: 58px; margin-bottom: 19px;
  }
  .service-icon {
    width: 58px; height: 58px; border-radius: 50%; background: var(--navy);
    display: flex; align-items: center; justify-content: center; flex-shrink: 0;
  }
  .service-name {
    margin-left: 11px; font-size: 14.5px; line-height: 17.5px; font-weight: 600; color: var(--white);
  }
  .booking {
    position: absolute; left: 0; top: 545px; width: 340px; height: 55px; background: var(--white);
    text-align: center; color: var(--navy);
  }
  .booking-label { font-size: 11.5px; font-weight: 500; padding-top: 4px; letter-spacing: .2px; }
  .booking-phone {
    display: flex; align-items: center; justify-content: center; gap: 4px;
    font-size: 26px; font-weight: 700; line-height: 28px; letter-spacing: .3px;
  }
  .back-name {
    position: absolute; left: 0; top: 600px; width: 340px; height: 80px;
    display: flex; align-items: center; justify-content: center;
    font-size: 26px; font-weight: 700; color: var(--white);
  }
</style>
</head>
<body>

<section class="flyer flyer--front">
  <svg class="front-art" width="340" height="680" viewBox="0 0 340 680">
    <defs>
      <linearGradient id="treatmentPhoto" x1="0" y1="0" x2="1" y2="1">
        <stop offset="0" stop-color="#f3ece6"/>
        <stop offset=".45" stop-color="#e8b895"/>
        <stop offset=".75" stop-color="#d99c78"/>
        <stop offset="1" stop-color="#efe6e4"/>
      </linearGradient>
    </defs>
    <circle cx="335" cy="125" r="40" fill="none" stroke="var(--blue-light)" stroke-width="14" opacity=".55"/>
    <polygon points="0,205 340,135 340,465 0,535" fill="url(#treatmentPhoto)" role="img" aria-label="Photo of a therapist's hands massaging a client's hand on a white towel"/>
    <circle cx="172" cy="335" r="142" fill="none" stroke="#9a9a9c" stroke-width="26" opacity=".35"/>
    <circle cx="318" cy="570" r="40" fill="none" stroke="var(--blue-bright)" stroke-width="14" opacity=".8"/>
    <circle cx="20" cy="705" r="55" fill="none" stroke="var(--blue-bright)" stroke-width="16" opacity=".8"/>
  </svg>
  <h1 class="front-title">LEIBESWERKSTATT</h1>
  <div class="front-rule"></div>
  <p class="front-subtitle">Physiotherapy</p>
  <p class="front-overlay-word">PHYSIOTHERAPY</p>
  <address class="front-contact" style="font-style:normal">
    <p class="name">Leibeswerkstatt,</p>
    <p class="address">Lindenweg 17,<br>06548 Sangerhausen<br>Leibeswerkstatt-beispielort.de</p>
    <p class="tel">Tel. 03464 7183520</p>
  </address>
</section>

<section class="flyer flyer--back">
  <p class="back-intro">Leibeswerkstatt understand that you have individual needs and we will make your treatment plan so that it is specific to you.</p>
  <div class="back-photo" role="img" aria-label="Photo of a woman stretching backwards over an exercise ball, tinted blue"
       style="background: linear-gradient(160deg, #0a6fb0 0%, #1b8fcf 45%, #2c9ad6 70%, #1279b8 100%);"></div>
  <p class="back-lead">We offer specialist care<br>in the following area's;</p>
  <div class="back-lead-rule"></div>
  <ul class="service-list">
    <li class="service">
      <span class="service-icon">
        <svg width="34" height="34" viewBox="0 0 34 34" fill="#fff"><circle cx="20" cy="7" r="4"/><rect x="14" y="12" width="12" height="8" rx="2"/><rect x="4" y="22" width="26" height="4" rx="1"/><rect x="4" y="28" width="26" height="2"/></svg>
      </span>
      <span class="service-name">Manual Therapy</span>
    </li>
    <li class="service">
      <span class="service-icon">
        <svg width="34" height="34" viewBox="0 0 34 34" fill="none" stroke="#fff" stroke-width="2.2"><circle cx="17" cy="9" r="6"/><path d="M6 31c0-8 5-13 11-13s11 5 11 13"/><path d="M17 18v13M11 24l6 3 6-3"/></svg>
      </span>
      <span class="service-name">Manual Lymphatic<br>Drainage</span>
    </li>
    <li class="service">
      <span class="service-icon">
        <svg width="34" height="34" viewBox="0 0 34 34" fill="#fff"><circle cx="11" cy="6" r="4"/><rect x="8" y="11" width="7" height="10" rx="2"/><circle cx="24" cy="19" r="4"/><rect x="4" y="23" width="26" height="4" rx="2"/><rect x="4" y="29" width="26" height="2"/></svg>
      </span>
      <span class="service-name">Classic Massage</span>
    </li>
    <li class="service">
      <span class="service-icon">
        <svg width="34" height="34" viewBox="0 0 34 34"><path d="M19 19s-9-5-9-11a4.5 4.5 0 0 1 9-1 4.5 4.5 0 0 1 9 1c0 6-9 11-9 11z" fill="#fff"/><path d="M19 8v6M16 11h6" stroke="var(--navy)" stroke-width="2"/><path d="M3 26l7-4h8l-2 3h-5M10 30h10l10-8" fill="none" stroke="#fff" stroke-width="2.4" stroke-linecap="round"/></svg>
      </span>
      <span class="service-name">Sectoral Alternative<br>Practitioner</span>
    </li>
  </ul>
  <div class="booking">
    <p class="booking-label">BOOK YOUR APPONTMENT TODAY ON</p>
    <p class="booking-phone">
      <svg width="22" height="22" viewBox="0 0 24 24" fill="var(--navy)"><path d="M6.6 10.8c1.4 2.8 3.8 5.1 6.6 6.6l2.2-2.2c.3-.3.7-.4 1-.2 1.1.4 2.3.6 3.6.6.6 0 1 .4 1 1V20c0 .6-.4 1-1 1C10.6 21 3 13.4 3 4c0-.6.4-1 1-1h3.5c.6 0 1 .4 1 1 0 1.3.2 2.5.6 3.6.1.3 0 .7-.2 1z"/></svg>
      03464 7183520
    </p>
  </div>
  <p class="back-name">Leibeswerkstatt</p>
</section>

</body>
</html>
```